Flat bootstrap design for existing site

I'm looking for a modern flat design based around an existing logo. This has to be a custom design (no external templates), and implemented into a bootstrap framework.

The logo is attached as 2 versions - choose whichever you want, that flows better with whatever design you choose.

Added screenshots of the existing site (currently using the default bootstrap layouts). Please make your designs around those pages in the screenshots (i.e. the homepage only has the postal code input and the header). The active page has 3 screenshots, because I wanted to illustrate the other states that would be visible (in the table rows).

This is a moving/junk removal website, just for some context.

Here's some example websites (flat designs) that I like, just to give you an idea of what I'm after.

https://www.plimvora.com/
https://dacklow.com/
https://trevanu.com/
https://quobrintal.com/en/

Coding

Coded - Design and coding required

Number of Pages Required

5+ page

Colors

Designer to choose colors to be used in the design.

Requirements
Must have
• It must be a modern/simple flat design, that is built around the existing logo (attached).
• It has to be implemented using bootstrap.

```html
<!DOCTYPE html>
<html lang="en">
<head>
<meta charset="utf-8">
<title>Haulveo – Book Details</title>
<link href="https://fonts.googleapis.com/css2?family=Mulish:wght@400;600;700;800&display=swap" rel="stylesheet">
<style>
:root{
  --brand:#4ac8f5;
  --brand-soft:#8adcf7;
  --brand-deep:#1b9bd1;
  --accept:#8ccc3a;
  --pending:#6b6b6b;
  --page:#e6e6e6;
  --ink:#4a4a4a;
  --muted:#7a7a7a;
  --rule:#cfcfcf;
  --head-row:#ececec;
  --footer:#f6f6f6;
  --white:#ffffff;
}
*{box-sizing:border-box;margin:0;padding:0}
html,body{width:1200px;height:1100px;overflow:hidden}
body{position:relative;background:var(--page);font-family:"Mulish",sans-serif;color:var(--ink)}
.site-header{position:absolute;left:0;top:0;width:1200px;height:114px;background:var(--white)}
.brand{position:absolute;left:83px;top:36px;display:flex;align-items:center;gap:10px;color:var(--brand);font-weight:800;font-size:38px;letter-spacing:1px}
.brand-mark{width:22px;height:22px;border-radius:50%;background:var(--brand)}
.main-nav{position:absolute;top:46px;left:470px;display:flex;gap:39px;font-size:17.5px;color:#6d6d6d;letter-spacing:.3px}
.user-menu{position:absolute;top:46px;left:933px;font-size:15px;color:#6d6d6d;display:flex;align-items:center;gap:6px}
.booking-panel{position:absolute;left:86px;top:147px;width:1027px;height:362px;background:var(--brand);color:var(--white)}
.panel-title{position:absolute;left:46px;top:28px;font-size:30px;font-weight:700}
.field-label{position:absolute;font-size:18px;font-weight:600}
.field{position:absolute;height:44px;background:var(--white);box-shadow:0 2px 4px rgba(0,0,0,.12);display:flex;align-items:center;justify-content:space-between;padding:0 13px;font-size:16px;color:#8a8a8a}
.btn-update{position:absolute;left:43px;top:278px;width:155px;height:47px;border:3px solid var(--white);border-radius:24px;display:flex;align-items:center;justify-content:center;font-size:18px;font-weight:700}
.section-title{position:absolute;left:93px;top:553px;font-size:30px;font-weight:800;color:var(--muted)}
.notice{position:absolute;left:91px;top:606px;width:1028px;height:48px;background:var(--brand-soft);color:var(--white);font-size:15.5px;padding:14px 0 0 36px}
.drivers{position:absolute;left:91px;top:654px;width:1028px;height:314px;background:var(--white)}
.table-head{position:absolute;left:28px;top:19px;width:957px;height:39px;background:var(--head-row);font-size:16px;font-weight:600;color:#2e2e2e}
.table-head span,.row span{position:absolute}
.table-head span{top:11px}
.row{position:absolute;left:36px;width:960px;height:48px;font-size:15px;color:#555}
.row.divided{border-bottom:1px solid var(--rule)}
.badge{position:absolute;width:120px;height:26px;color:var(--white);font-size:13px;font-weight:600;display:flex;align-items:center;justify-content:center}
.badge.accepted{background:var(--accept)}
.badge.sent{background:var(--brand)}
.badge.pending{background:var(--pending)}
.badge.pay{background:var(--brand-deep)}
.site-footer{position:absolute;left:0;top:1018px;width:1200px;height:82px;background:var(--footer);text-align:center;padding-top:26px;font-size:15.5px;color:#7a7a7a}
</style>
</head>
<body>
<header class="site-header">
  <div class="brand"><span class="brand-mark"></span>HAULVEO</div>
  <nav class="main-nav"><span>BOOK</span><span>HOW IT WORKS</span><span>BECOME A DRIVER</span></nav>
  <div class="user-menu">marta@plenvoq.com
    <svg width="16" height="10" viewBox="0 0 16 10"><path d="M1 1l7 7 7-7" fill="none" stroke="#6d6d6d" stroke-width="1.6"/></svg>
  </div>
</header>

<section class="booking-panel">
  <h1 class="panel-title">Book Details</h1>
  <div class="field-label" style="left:44px;top:83px">Package Selected:</div>
  <div class="field-label" style="left:523px;top:83px">Pick-up time selected</div>
  <div class="field" style="left:44px;top:113px;width:465px">Package 1
    <svg width="18" height="11" viewBox="0 0 18 11"><path d="M1 1l8 8 8-8" fill="none" stroke="#777" stroke-width="1.6"/></svg>
  </div>
  <div class="field" style="left:522px;top:113px;width:465px">July 18 at 4:13 am
    <svg width="18" height="18" viewBox="0 0 18 18" fill="none" stroke="#999" stroke-width="1.2"><rect x="1" y="3" width="16" height="14"/><path d="M1 7h16M5 1v4M13 1v4M5 10h2M9 10h2M13 10h1M5 13h2M9 13h2M13 13h1"/></svg>
  </div>
  <div class="field-label" style="left:46px;top:179px">Description</div>
  <div class="field" style="left:46px;top:209px;width:941px">1 Large stove</div>
  <div class="btn-update">Update</div>
</section>

<h2 class="section-title">Drivers in your area</h2>
<div class="notice">Please stay on this page and be patient, while we contact the driver and find you one ASAP</div>

<section class="drivers">
  <div class="table-head">
    <span style="left:21px">Name</span>
    <span style="left:199px">Distance</span>
    <span style="left:399px">Agreed pick-up time</span>
  </div>
  <div class="row divided" style="top:67px">
    <span style="left:2px;top:17px">Dorian Vale</span>
    <span style="left:176px;top:17px">4.04 km away</span>
    <span style="left:389px;top:15px">July 18 at 4:13 am</span>
    <div class="badge accepted" style="left:608px;top:10px">Time accepted</div>
    <div class="badge pay" style="left:786px;top:9px">Make payment</div>
  </div>
  <div class="row divided" style="top:115px">
    <span style="left:2px;top:17px">Felix Marrow</span>
    <span style="left:176px;top:17px">5.75 km away</span>
    <span style="left:389px;top:13px">-</span>
    <div class="badge sent" style="left:609px;top:11px">Request sent</div>
  </div>
  <div class="row divided" style="top:163px;height:52px">
    <span style="left:2px;top:17px">Oswin Tarrant</span>
    <span style="left:176px;top:17px">11.13 km away</span>
    <span style="left:389px;top:13px">-</span>
    <div class="badge sent" style="left:609px;top:11px">Request sent</div>
  </div>
  <div class="row" style="top:215px">
    <span style="left:2px;top:13px">Ravi Dellacourt</span>
    <span style="left:176px;top:13px">11.91 km away</span>
    <span style="left:389px;top:9px">-</span>
    <div class="badge pending" style="left:611px;top:10px">Pending</div>
  </div>
</section>

<footer class="site-footer">© 2017 Company Name&nbsp; All right reserved&nbsp; Term of Use</footer>
</body>
</html>
```